New business card for a regional office of a US M&A company

We need business card for a finance company, office based in Hong Kong , our Head office is in US, our business is to Merge and acquires companies , the new office will be a regional office for the Asia Pacific region. We want to use the head office logo as attached ( but don't have to be exactly the same, can be a variation to it) as a base and then add Asia Pacific alongside the logo.
We would prefer to have be bilingual Eng + Chinese, although we don't really have Chinese company name .

Industry/Entity Type

Business

Contact Information for Business Card

Clara Jo Tsang
 

VP,
APAC M&A Operations
Orin Vantage Asia Pacific Limited
 
Unit 1407, K18
18 Tai Lok Shan Road, 
Hong Kong 
 
M: +852 6038 1742
T : +852 2836 4100
F : +852 2836 4177
VOIP: 4158
 
cjtsang@orinvantage.com

Font styles to use
Serif
Sans Serif

Colors

Designer to choose colors to be used in the design.

Requirements
Must have
• APAC Office

```html
<!DOCTYPE html>
<html lang="en">
<head>
<meta charset="utf-8">
<title>Orin Vantage – APAC Business Card</title>
<link rel="stylesheet" href="https://fonts.googleapis.com/css2?family=Open+Sans:wght@800&family=Roboto:wght@400;500&family=Roboto+Condensed:wght@700&display=swap">
<style>
  :root {
    --page-bg: #e4e1dc;
    --navy: #0f2a45;
    --paper: #ebeff2;
    --cyan: #1ea8d4;
    --light-text: #e3e8ee;
    --white: #ffffff;
    --grey-text: #4a4f55;
  }
  * { margin: 0; padding: 0; box-sizing: border-box; }
  html, body { width: 1200px; height: 960px; overflow: hidden; }
  body { position: relative; background: var(--page-bg); font-family: "Roboto", Arial, sans-serif; }

  .card { position: absolute; width: 600px; height: 343px; }
  .card--front { left: 314px; top: 113px; background: var(--navy); }
  .card--back { left: 311px; top: 472px; background: var(--paper); }

  .brand-name {
    font-family: "Open Sans", Arial, sans-serif;
    font-weight: 800;
    color: var(--cyan);
    white-space: nowrap;
    letter-spacing: -0.5px;
  }
  .card--front .brand-name { position: absolute; left: 31px; top: 113px; font-size: 38px; line-height: 1; }

  .office-details {
    position: absolute; left: 33px; top: 195px;
    color: var(--light-text); font-size: 14.5px; line-height: 18.5px;
  }
  .office-details .contact-row { margin-top: 6px; display: flex; align-items: center; gap: 4px; }
  .office-details .voip { margin-top: 5px; }
  .icon { width: 13px; height: 13px; fill: var(--cyan); flex: none; }

  .person {
    position: absolute; right: 37px; top: 224px; text-align: right; color: var(--white);
  }
  .person__name {
    font-family: "Roboto Condensed", Arial, sans-serif; font-weight: 700;
    font-size: 20px; color: var(--cyan); text-transform: uppercase; line-height: 24px;
  }
  .person__title, .person__mobile { font-size: 14.5px; line-height: 21px; }

  .card--back .brand-name {
    position: absolute; left: 0; right: 0; top: 188px; text-align: center; font-size: 48px; line-height: 1;
  }
  .website {
    position: absolute; left: 0; right: 0; top: 284px; text-align: center;
    font-size: 15px; letter-spacing: 8.3px; color: var(--grey-text);
  }
</style>
</head>
<body>
  <section class="card card--front">
    <div class="brand-name">ORIN VANTAGE</div>

    <div class="office-details">
      <p>APAC M&amp;A Operations</p>
      <p>Orin Vantage Asia Pacific Limited</p>
      <p>Unit 1407, K18, 18 Tai Lok Shan Road</p>
      <p>Hong Kong</p>
      <p class="contact-row">
        <svg class="icon" viewBox="0 0 24 24" aria-hidden="true"><path d="M6.6 10.8c1.4 2.8 3.8 5.1 6.6 6.6l2.2-2.2c.3-.3.7-.4 1-.2 1.1.4 2.3.6 3.6.6.6 0 1 .4 1 1V20c0 .6-.4 1-1 1C10.6 21 3 13.4 3 4c0-.6.4-1 1-1h3.5c.6 0 1 .4 1 1 0 1.3.2 2.5.6 3.6.1.3 0 .7-.2 1z"/></svg>
        <span>+852 2836 4100</span>
        <svg class="icon" viewBox="0 0 24 24" aria-hidden="true"><path d="M6 3h12v5H6zM3 9h18v9h-3v-3H6v3H3zM7 16h10v5H7z"/></svg>
        <span>+852 2836 4177</span>
      </p>
      <p class="voip">VOIP: 4158</p>
    </div>

    <div class="person">
      <p class="person__name">Clara Jo Tsang</p>
      <p class="person__title">VP</p>
      <p class="person__mobile">+852 6038 1742</p>
    </div>
  </section>

  <section class="card card--back">
    <div class="brand-name">ORIN VANTAGE</div>
    <p class="website">www.orinvantage.com</p>
  </section>
</body>
</html>
```